develop our online residential property development appraisal service

This project requires a detailed WordPress design to represent a new digital residential property development consultancy business. At its heart it will have a number of different products that essentially advise customers of the potential value and feasibility of developing their residential site into multiple townhouses, units, apartments, etc... This will be accompanied by explaining the considerations of residential property development.

We aim to navigate and break down this complex area and provide our customers with the tools, knowledge, control and power to 'unlock the value' in their property.

REFERENCE DOCUMENTS:
1. Detailed solution requirements please refer to the attached 'wordpressdesignrequirements'
2. Logo files, style guide and colour pallet please refer to the attached 'KRLM.zip'
3. Site Map refer to attached 'wordpressdesignsitemap'

Reason: Additional information provided so extending period for designs to take into account.

Target Market(s)

The site will appeal to professional service providers; accountants, financial planners, lawyers, etc…

Industry/Entity Type

Residential

Font styles to use
Sans Serif
Other font styles liked:
• Similar to the logo font, slim line and simple

Requirements
Must have
• The logo, style and colour palette provided in the attached 'KRLM.zip' files
• Satisfy the intent of the 'wordpressdesignrequirements'
• Present as an online-centric business
• Clean, crisp and modern design
• Predominant use of white as a background contrasted with the colours provided in the colour palette
Nice to have
• Use of the following WordPress business themes is encouraged but not mandatory:
• 1. Mavo
• 2. Tulek
• 3. Vupa
Should not have
• Overt references to Australia

```html
<!DOCTYPE html>
<html lang="en">
<head>
<meta charset="utf-8">
<title>KRLM – Residential Property Development Appraisal</title>
<link href="https://fonts.googleapis.com/css2?family=Open+Sans:wght@300;400;600;700&display=swap" rel="stylesheet">
<style>
:root{
  --teal:#2fb3a2;
  --teal-dark:#23907f;
  --teal-light:#d3ece8;
  --ink:#2b2f33;
  --ink-deep:#222528;
  --panel:#34393e;
  --text:#5a5f63;
  --muted:#9aa1a5;
  --orange:#e3803c;
  --white:#ffffff;
  --line:#e3e6e8;
}
*{box-sizing:border-box;margin:0;padding:0}
html,body{width:793px;height:1200px;overflow:hidden}
body{position:relative;background:var(--white);font-family:'Open Sans',sans-serif;color:var(--text);font-size:8px;line-height:1.5}
.abs{position:absolute}
ul{list-style:none}

/* top bar */
.topbar{left:0;top:0;width:793px;height:22px;background:var(--ink-deep);color:var(--muted);font-size:7px;display:flex;align-items:center;justify-content:space-between;padding:0 40px}
.topbar .socials{display:flex;gap:5px;align-items:center}
.topbar .socials span{width:9px;height:9px;border-radius:50%;background:#4a5055;display:block}

/* hero */
.hero{left:0;top:22px;width:793px;height:270px;background:linear-gradient(180deg,#3b4a55 0%,#6f7f86 45%,#a9a196 70%,#4d5a4c 100%)}
.header{left:0;top:22px;width:793px;height:42px;background:rgba(30,33,36,.75);display:flex;align-items:center;padding:0 40px}
.brand{display:flex;align-items:center;gap:7px}
.brand-mark{width:20px;height:20px;background:var(--teal)}
.brand-name{font-size:18px;font-weight:300;color:var(--teal);letter-spacing:1px}
.brand-tag{font-size:6px;color:#c9cfd2;line-height:1.25;width:90px;margin-left:2px}
.nav{position:absolute;left:385px;top:10px;display:flex;gap:2px}
.nav a{display:block;color:#e4e8ea;font-size:7.5px;padding:4px 9px;text-decoration:none}
.nav a.active{background:var(--teal);color:var(--white)}
.nav a.open{background:var(--white);color:var(--teal-dark)}
.search-top{position:absolute;right:40px;top:8px;width:44px;height:14px;background:#3e4449}
.dropdown{left:475px;top:58px;width:80px;background:var(--white);box-shadow:0 2px 4px rgba(0,0,0,.2)}
.dropdown li{font-size:7px;padding:4px 7px;border-bottom:1px solid var(--line);color:var(--ink)}
.dropdown li:first-child{background:var(--teal);color:var(--white)}
.hero-copy{left:40px;top:175px;width:300px}
.hero-copy h1{font-size:15px;font-weight:400;color:#7fe0d3;margin-bottom:4px}
.hero-copy p{color:#eef1f2;font-size:7.5px;margin-bottom:8px}
.btn{display:inline-block;background:var(--teal);color:var(--white);font-size:7px;padding:4px 9px}
.btn-orange{background:var(--orange)}

/* section headings */
.h2{font-size:13px;font-weight:400;color:var(--teal-dark);padding-bottom:4px;border-bottom:1px solid var(--line)}

/* know about */
.know{left:45px;top:305px;width:355px}
.tabs-panel{left:45px;top:338px;width:355px;height:248px;background:var(--panel)}
.tabs{position:absolute;right:10px;top:8px;display:flex;gap:3px}
.tabs span{font-size:7px;color:#d7dcde;background:#454b51;padding:3px 7px}
.tabs span.on{background:var(--ink-deep);color:var(--white)}
.tab-image{position:absolute;left:15px;top:40px;width:150px;height:120px;background:linear-gradient(170deg,#8fb3cf 0%,#d9dcd8 55%,#6f8a5a 100%)}
.tab-text{position:absolute;left:178px;top:40px;width:165px;color:#cfd5d8;font-size:7.5px}
.tab-panel-btn{position:absolute;right:15px;bottom:18px}

.opps{left:420px;top:305px;width:330px}
.opps ul{margin-top:10px}
.opps li{position:relative;padding-left:12px;margin-bottom:11px;font-size:7.5px}
.opps li::before{content:"";position:absolute;left:0;top:3px;width:5px;height:5px;background:var(--teal)}

/* recent */
.recent{left:0;top:598px;width:793px;height:164px;background:var(--teal-light)}
.recent-image{left:45px;top:610px;width:255px;height:140px;background:linear-gradient(170deg,#a9c4d6 0%,#e7e6e1 55%,#8c9478 100%)}
.recent-copy{left:320px;top:615px;width:430px}
.recent-copy h3{font-size:8.5px;color:var(--ink);font-weight:700;margin:6px 0 3px}
.recent-copy p{font-size:7.5px;margin-bottom:8px}

/* reports */
.reports{left:45px;top:778px;width:703px}
.card{top:810px;width:195px}
.card-image{width:195px;height:135px}
.card-row{display:flex;justify-content:space-between;align-items:center;margin-top:9px}
.card-row b{font-size:8px;color:var(--ink);font-weight:600}
.dots{left:0;top:985px;width:793px;display:flex;justify-content:center;gap:3px}
.dots span{width:8px;height:8px;background:var(--teal)}
.dots span.off{background:#9fd6cd}

/* footer */
.footer{left:0;top:1005px;width:793px;height:195px;background:var(--ink)}
.fcol{top:1020px}
.fcol h4{font-size:10px;font-weight:400;color:var(--teal);margin-bottom:6px}
.fcol li{font-size:7px;color:#b6bcc0;margin-bottom:5px}
.fsearch{width:180px;height:15px;background:#3e4449;margin-bottom:14px}
.fcontact li{display:flex;gap:6px;align-items:center}
.copyright{left:0;top:1172px;width:793px;height:28px;border-top:1px solid #3d4247;font-size:7px;color:var(--muted);padding:9px 45px}
</style>
</head>
<body>

<div class="abs topbar">
  <span>hello@krlmappraisal.com</span>
  <div class="socials"><span></span><span></span><span></span><span></span><span style="background:none;width:auto;height:auto">Login | Register</span></div>
</div>

<div class="abs hero" role="img" aria-label="Photograph of a modern two-storey townhouse at dusk"></div>

<header class="abs header">
  <div class="brand">
    <span class="brand-mark"></span>
    <span class="brand-name">KRLM</span>
    <span class="brand-tag">Residential Property Development Appraisal</span>
  </div>
  <nav class="nav">
    <a class="active">Home</a>
    <a>About Us</a>
    <a class="open">Property Report</a>
    <a>Property Development</a>
    <a>Contact us</a>
  </nav>
  <div class="search-top"></div>
</header>
<ul class="abs dropdown">
  <li>Property Report A</li>
  <li>Property Report B</li>
  <li>Property Report C</li>
</ul>

<div class="abs hero-copy">
  <h1>Neque Porro Quisquam Est</h1>
  <p>Sed ut perspiciatis unde omnis iste natus error sit voluptatem accusantium doloremque laudantium totam rem.</p>
  <span class="btn">Read More</span>
</div>

<section class="abs know"><h2 class="h2">Know About US</h2></section>
<div class="abs tabs-panel">
  <div class="tabs"><span class="on">WHO we are?</span><span>WHAT we do?</span><span>HOW do we do it?</span></div>
  <div class="tab-image" role="img" aria-label="Photograph of a contemporary family house"></div>
  <p class="tab-text">We aim to navigate and break down the complex area of residential property development, giving you the tools, knowledge, control and power to unlock value.</p>
  <span class="btn tab-panel-btn">Read More</span>
</div>

<section class="abs opps">
  <h2 class="h2">Opportunities</h2>
  <ul>
    <li>Find out the potential value and feasibility of developing your residential site.</li>
    <li>Compare townhouse, unit and apartment options side by side for your block.</li>
    <li>Understand planning, costs and timing before you commit to a project.</li>
    <li>Share clear reports with your accountant, planner or lawyer in minutes.</li>
    <li>Order a tailored appraisal online and receive expert advice by email.</li>
  </ul>
</section>

<div class="abs recent"></div>
<div class="abs recent-image" role="img" aria-label="Photograph of a recently completed residential development"></div>
<section class="abs recent-copy">
  <h2 class="h2">Recent Property Development</h2>
  <h3>Soluta Nobis Est</h3>
  <p>Temporibus autem quibusdam et aut officiis debitis aut rerum necessitatibus saepe eveniet ut et voluptates repudiandae sint et molestiae non recusandae itaque earum rerum hic tenetur.</p>
  <span class="btn">Read More</span>
</section>

<section class="abs reports"><h2 class="h2">Property Report Summary</h2></section>
<div class="abs card" style="left:45px">
  <div class="card-image" role="img" aria-label="Photograph of a single-storey house with front garden" style="background:linear-gradient(170deg,#b9cfe0 0%,#d8d2c6 55%,#7d8f62 100%)"></div>
  <div class="card-row"><b>Property Report A</b><span class="btn btn-orange">Request Report</span></div>
</div>
<div class="abs card" style="left:299px">
  <div class="card-image" role="img" aria-label="Photograph of a modern townhouse at night" style="background:linear-gradient(170deg,#2f3e52 0%,#6c7480 55%,#b59a72 100%)"></div>
  <div class="card-row"><b>Property Report B</b><span class="btn btn-orange">Request Report</span></div>
</div>
<div class="abs card" style="left:553px">
  <div class="card-image" role="img" aria-label="Photograph of a contemporary apartment building" style="background:linear-gradient(170deg,#9ec0dd 0%,#e2e3e1 55%,#8d8f86 100%)"></div>
  <div class="card-row"><b>Property Report C</b><span class="btn btn-orange">Request Report</span></div>
</div>
<div class="abs dots"><span></span><span class="off"></span></div>

<footer class="abs footer"></footer>
<div class="abs fcol" style="left:45px">
  <h4>About Us</h4>
  <ul><li>WHO we are?</li><li>WHAT we do?</li><li>HOW do we do it?</li></ul>
</div>
<div class="abs fcol" style="left:330px">
  <h4>Links</h4>
  <ul><li>About Us</li><li>Opportunities</li><li>Property Report</li><li>Property Development</li><li>Contact Us</li><li>Site Map</li></ul>
</div>
<div class="abs fcol" style="left:560px">
  <h4>Search</h4>
  <div class="fsearch"></div>
  <h4>Contact Us</h4>
  <ul class="fcontact">
    <li><svg width="8" height="8" viewBox="0 0 8 8"><rect x="0.5" y="1.5" width="7" height="5" fill="none" stroke="#2fb3a2"/><path d="M0.5 1.5 4 4.5 7.5 1.5" fill="none" stroke="#2fb3a2"/></svg>hello@krlmappraisal.com</li>
    <li><svg width="8" height="8" viewBox="0 0 8 8"><path d="M1 1h2l1 2-1 1a4 4 0 0 0 2 2l1-1 2 1v2C4 8 0 4 1 1z" fill="#2fb3a2"/></svg>+00 123 456 789</li>
  </ul>
</div>
<div class="abs copyright">© Copyright information here</div>

</body>
</html>
```